physio rehab flyer for Vela Mend please

Specification:
Flyer is to be trifold from letter size (8.5 x 11)
-----------------------This may help you:--------------------------
I would like the look of :
clean, minimalistic look with mainly blue and green
san serif font
professional
The colors I like are blue (not the blue in the logo enclosed, I want a change, but more like the blue on my website logo) and light green.
This is my website: www.velamendgroup.ca just so you get an idea but it will be totally changed soon to a to be determined design.
I like the blue and green in file "sample 2" (enclosed)
I like the pictures in "sample 2" file enclosed
For inspiration, I like design of this brochure: http://www.brelford.ca/HarlowRehab/PatientsFamilies/Clinics_Tests/DKAP_Service/Documents/Brochure.pdf
Here's how I see the pages layout:
----[location: this should be the cover (outside, right panel of trifold)]-----
Vela Mend Logo
Integrated Injury Rehab
Evidence-based, one-on-one care to make your recovery fast and comfortable
www.velamendgroup.ca
---------------[location: inside, left panel]----------------------------------------
Our team leaders
[portrait here]
Harriet Olsavik, MD, FRCPC, MSC, CIME
Physiatrist
Dr. Olsavik specializes in injury rehab and sports medicine. She is highly trained having received her MD and Residency in Physiatry from Pellham Institute. Her passion is to help injured people get back to their life.
[portrait here]
Wendy Carstairs, PT
Physiotherapist
Wendy has over 10 years of experience as a Physiotherapist (5 in Canada). She has advanced training in orthopedics and manual therapy. She loves and relates well with people from the youngest to the most senior.
--------------------[location: inside, middle panel]-------------------------------
Our services
We provide integrated assessment and care from interprofessional team of regulated healthcare professionals with proven experience in injury rehabilitation:
physiatrists
sport medicine physicians
physiotherapists
chiropractors
massage therapists
acupuncturists
psychologists
We provide custom medical bracing, orthotics, orthopedic shoes, assistive devices, and medical stockings, all in one place.
----------------------[location: inside, right panel]-----------------------------------
Only registered physiotherapists
We strongly believe in consistency with your treatment plan. This means that you spend your time here one-on-one with your physiotherapist, not any students or assistants. You get consistent high quality care from a professional.
One-on-one attention
We book maximum 3 people per hour to ensure everyone gets adequate one-on-one time with their physiotherapist. This compares favorably with other clinics, who may book upwards of 5-6 per hour. The atmosphere is professional -balanced with friendly, caring and relaxed. Our highly qualified staff operate this way to help make your recovery faster and more enjoyable.
------------------------[location: outside, left panel]---------------------------------
The right rehab for your clients
Timely access to comprehensive assessment and treatment
Proven track record in injury rehabilitation
Convenient one-stop service
Customized treatment plans
Integrated, co-ordinated care
Evidence-based care applying leading best practices
Access to specialty clinics: Physiatry and Chronic Pain
-------------------------[location: outside, middle panel]--------------------------
Please call us 555-384-2096
for more information on injury rehabilitation
Vela Mend Group
1862 Wexmoor Rd., Unit 9
Scarborough, ON K4T 8B2
[Please include a line art map designed based on "map" file enclosed]
To make a referral for your clients, contact velamendgroup@corvamail.ca or fax: 555-384-2071. Thank you.
www.velamendgroup.ca
------------------------------------------------------------------------------------------------
Target Market(s)
family doctors, ER docs, lawyers, and general public age (20-50)
Industry/Entity Type
Health And Wellness
Requirements
Must have
- san serif font
- blue and green colors
- clean, sophisticated look
Nice to have
- consumer choice award badge either on front or back of trifold
- see above

```html
<!DOCTYPE html>
<html lang="en">
<head>
<meta charset="utf-8">
<title>Vela Mend – Inside Spread</title>
<link href="https://fonts.googleapis.com/css2?family=Ubuntu:wght@300;400;700&display=swap" rel="stylesheet">
<style>
  :root {
    --backdrop: #3c3c3c;
    --paper: #ffffff;
    --brand-blue: #4a80c9;
    --brand-blue-deep: #2f63b3;
    --heading-blue: #3d70be;
    --wave-light: #dfe9f6;
    --ink: #555a60;
    --ink-soft: #61666c;
    --photo-tone-a: #cfd9e6;
    --photo-tone-b: #eef2f7;
  }
  * { box-sizing: border-box; margin: 0; padding: 0; }
  html, body { width: 1200px; height: 1200px; overflow: hidden; }
  body { background: var(--backdrop); font-family: "Ubuntu", Arial, sans-serif; color: var(--ink); }

  .spread {
    position: absolute; left: 55px; top: 155px; width: 1091px; height: 842px;
    background: var(--paper); overflow: hidden;
  }
  .fold { position: absolute; top: 0; bottom: 0; width: 360px; }
  .fold--middle { left: 369px; background: linear-gradient(90deg, #f1f3f6 0%, #fff 12%, #fff 86%, #f0f2f5 100%); }
  .fold--right { left: 729px; width: 362px; background: linear-gradient(90deg, #f3f4f6 0%, #fff 10%); }

  .waves { position: absolute; inset: 0; width: 1091px; height: 842px; }

  .photo { position: absolute; }
  .photo--lead { left: 30px; top: 35px; width: 195px; height: 255px; background: radial-gradient(ellipse at 55% 45%, #f4f1ee 0%, #dfe3ea 60%, rgba(255,255,255,0) 100%); }
  .photo--second { left: 236px; top: 598px; width: 124px; height: 244px; background: radial-gradient(ellipse at 50% 50%, #d9c9c4 0%, #cfd3dc 55%, rgba(255,255,255,0) 100%); }
  .photo--treatment { left: 369px; top: 417px; width: 360px; height: 233px; background: linear-gradient(180deg, rgba(255,255,255,0) 0%, var(--photo-tone-a) 25%, var(--photo-tone-b) 80%, rgba(255,255,255,0) 100%); }

  .rule { position: absolute; left: 0; top: 291px; width: 367px; height: 2px; background: var(--brand-blue); }

  .name { position: absolute; color: var(--heading-blue); font-weight: 700; font-variant: small-caps; white-space: nowrap; }
  .name--lead { left: 55px; top: 309px; font-size: 14.5px; letter-spacing: 0; }
  .name--second { left: 34px; top: 526px; font-size: 16px; letter-spacing: 0.3px; }
  .role { position: absolute; color: var(--heading-blue); font-size: 14px; letter-spacing: 0.3px; }
  .bio { position: absolute; font-size: 14px; line-height: 16.5px; letter-spacing: 0.5px; color: var(--ink-soft); font-weight: 300; }
  .bio--lead { left: 56px; top: 364px; width: 259px; }
  .bio--second { left: 35px; top: 582px; width: 196px; }

  .line { display: block; white-space: nowrap; text-align: justify; text-align-last: justify; }
  .line--short { text-align: left; text-align-last: left; }

  .section-title { position: absolute; color: var(--heading-blue); font-weight: 700; font-variant: small-caps; font-size: 17px; letter-spacing: 0.3px; white-space: nowrap; }
  .copy { position: absolute; font-size: 14px; font-weight: 300; letter-spacing: 0.7px; color: var(--ink); }
  .copy--services { left: 396px; top: 100px; width: 311px; line-height: 25px; }
  .copy--products { left: 396px; top: 687px; width: 311px; line-height: 25px; }
  .copy--right { left: 751px; width: 311px; line-height: 36px; }

  .service-list { position: absolute; left: 419px; top: 211px; list-style: none; font-size: 14px; font-weight: 300; letter-spacing: 0.7px; color: var(--ink); }
  .service-list li { height: 25px; display: flex; align-items: center; }
  .service-list svg { width: 13px; height: 11px; margin-right: 23px; }
</style>
</head>
<body>
  <main class="spread">
    <div class="fold fold--middle"></div>
    <div class="fold fold--right"></div>

    <svg class="waves" viewBox="0 0 1091 842" aria-hidden="true">
      <defs>
        <linearGradient id="softWave" x1="0" y1="0" x2="1" y2="0">
          <stop offset="0" stop-color="#ffffff" stop-opacity="0.9"/>
          <stop offset="1" stop-color="#c9d9ef" stop-opacity="0.6"/>
        </linearGradient>
      </defs>
      <path d="M0 0 H735 C560 8 320 55 160 112 C90 138 40 160 0 180 Z" fill="var(--brand-blue)"/>
      <path d="M0 180 C60 150 150 110 260 80 C180 140 120 180 60 200 Z" fill="#ffffff" opacity="0.9"/>
      <path d="M170 150 C260 60 420 20 735 0 C520 30 360 80 260 150 C230 170 200 175 170 150 Z" fill="url(#softWave)" opacity="0.8"/>
      <path d="M140 165 C300 60 500 18 730 2" fill="none" stroke="#ffffff" stroke-width="1.5" opacity="0.8"/>
      <path d="M1091 610 C950 690 760 760 560 800 C700 770 900 720 1091 650 Z" fill="var(--wave-light)" opacity="0.8"/>
      <path d="M1091 680 C920 760 720 815 490 842 H1091 Z" fill="var(--brand-blue)"/>
      <path d="M1091 680 C920 760 720 815 490 842" fill="none" stroke="var(--brand-blue-deep)" stroke-width="3"/>
    </svg>

    <div class="photo photo--lead" role="img" aria-label="Portrait of the physiatrist in a white coat with stethoscope"></div>
    <div class="rule"></div>
    <div class="photo photo--second" role="img" aria-label="Portrait of the physiotherapist with arms folded"></div>
    <div class="photo photo--treatment" role="img" aria-label="Physiotherapist examining a patient's knee in a clinic"></div>

    <h2 class="name name--lead">Harriet Olsavik,&nbsp; MD, FRCPC, MSC, CIME</h2>
    <p class="role" style="left:55px;top:336px;">Physiatrist</p>
    <p class="bio bio--lead">
      <span class="line">Dr. Olsavik specializes in injury</span>
      <span class="line">rehab and sports medicine. She is</span>
      <span class="line">highly trained having received her</span>
      <span class="line">MD and Residency in Physiatry from</span>
      <span class="line">Pellham Institute. Her passion is</span>
      <span class="line">to help injured people get back to</span>
      <span class="line line--short">their life.</span>
    </p>

    <h2 class="name name--second">Wendy Carstairs, PT</h2>
    <p class="role" style="left:34px;top:551px;">Physiotherapist</p>
    <p class="bio bio--second">
      <span class="line line--short">Wendy has over 10 years of</span>
      <span class="line line--short">experience as a</span>
      <span class="line line--short">Physiotherapist</span>
      <span class="line line--short">(5 in Canada). She has</span>
      <span class="line line--short">advanced training in</span>
      <span class="line line--short">orthopedics and manual</span>
      <span class="line line--short">therapy. She loves and</span>
      <span class="line line--short">relates well with people</span>
      <span class="line line--short">from the youngest to</span>
      <span class="line line--short">the most senior.</span>
    </p>

    <h2 class="section-title" style="left:396px;top:70px;">Our services</h2>
    <p class="copy copy--services">
      <span class="line">We provide integrated assessment and care</span>
      <span class="line">from interprofessional team of regulated</span>
      <span class="line line--short">healthcare professionals with proven</span>
      <span class="line line--short">experience in injury rehabilitation:</span>
    </p>
    <ul class="service-list">
      <li><svg viewBox="0 0 13 11"><path d="M1 6 L5 10 L12 1" fill="none" stroke="var(--brand-blue)" stroke-width="2.6"/></svg>physiatrists</li>
      <li><svg viewBox="0 0 13 11"><path d="M1 6 L5 10 L12 1" fill="none" stroke="var(--brand-blue)" stroke-width="2.6"/></svg>sport medicine physicians</li>
      <li><svg viewBox="0 0 13 11"><path d="M1 6 L5 10 L12 1" fill="none" stroke="var(--brand-blue)" stroke-width="2.6"/></svg>physiotherapists</li>
      <li><svg viewBox="0 0 13 11"><path d="M1 6 L5 10 L12 1" fill="none" stroke="var(--brand-blue)" stroke-width="2.6"/></svg>chiropractors</li>
      <li><svg viewBox="0 0 13 11"><path d="M1 6 L5 10 L12 1" fill="none" stroke="var(--brand-blue)" stroke-width="2.6"/></svg>massage therapists</li>
      <li><svg viewBox="0 0 13 11"><path d="M1 6 L5 10 L12 1" fill="none" stroke="var(--brand-blue)" stroke-width="2.6"/></svg>acupuncturists</li>
      <li><svg viewBox="0 0 13 11"><path d="M1 6 L5 10 L12 1" fill="none" stroke="var(--brand-blue)" stroke-width="2.6"/></svg>psychologists</li>
    </ul>
    <p class="copy copy--products">
      <span class="line line--short">We provide custom medical bracing,</span>
      <span class="line line--short">orthotics, orthopedic shoes, assistive</span>
      <span class="line">devices, and medical stockings, all in one</span>
      <span class="line line--short">place.</span>
    </p>

    <h2 class="section-title" style="left:751px;top:42px;">Only registered physiotherapists</h2>
    <p class="copy copy--right" style="top:72px;">
      <span class="line">We strongly believe in consistency with</span>
      <span class="line">your treatment plan. This means that you</span>
      <span class="line">spend your time here one-on-one with</span>
      <span class="line">your physiotherapist, not any students or</span>
      <span class="line">assistants. You get consistent high quality</span>
      <span class="line line--short">care from a professional.</span>
    </p>
    <h2 class="section-title" style="left:751px;top:305px;">Only registered physiotherapists</h2>
    <p class="copy copy--right" style="top:334px;">
      <span class="line">We book maximum 3 people per hour to</span>
      <span class="line line--short">ensure everyone gets adequate</span>
      <span class="line line--short">one-on-one time with their</span>
      <span class="line">physiotherapist.&nbsp; This compares favorably</span>
      <span class="line">with other clinics, who may book upwards</span>
      <span class="line line--short">of 5-6 per hour. The atmosphere is</span>
      <span class="line">professional -balanced with friendly,</span>
      <span class="line">caring and relaxed. Our highly qualified</span>
      <span class="line">staff operate this way to help make your</span>
      <span class="line line--short">recovery faster and more enjoyable.</span>
    </p>
  </main>
</body>
</html>
```